Lanternfield Drinks business cards

We need a business card design for our new logo. The company is modern, progressive, professional, yet approachable. The key products are ready to drink bottles and cans of coffee based beverages.
These cards will be a critical part of the first impression made by our sales organization, business development team, and all external facing personnel.
Card can be a vertical or horizontal orientation.

Target Market(s)

Customers, suppliers, business partners

Industry/Entity Type

Business

Contact Information for Business Card

Business cards should feature Company Name and Logo.

Font styles to use
Serif

Colors

Designer to choose colors to be used in the design.

Requirements
Must have
• Strong readability of Name, phone #, mobile number and email address.
• Job title, website url, Street Address, and other details can be secondary level readability.
Nice to have
• High impact, simplistic quality design.
• Ok to utilize the 'H in the box' separate from the company name

```html
<!DOCTYPE html>
<html lang="en">
<head>
<meta charset="utf-8">
<title>Lanternfield Drinks – Business Cards</title>
<link rel="stylesheet" href="https://fonts.googleapis.com/css2?family=Crimson+Text:wght@400;600;700&display=swap">
<style>
  :root {
    --backdrop: #3b3b3c;
    --card-black: #232324;
    --card-front: #1f1f20;
    --orange: #e1552f;
    --gold: #f2982b;
    --white: #ffffff;
    --emboss: #5a5a5c;
    --emboss-light: #8b8b8d;
  }
  * { margin: 0; padding: 0; box-sizing: border-box; }
  html, body {
    width: 799px; height: 1200px; overflow: hidden;
    background: var(--backdrop);
    font-family: "Crimson Text", Georgia, serif;
  }
  .sheet {
    position: relative; width: 799px; height: 1200px;
    display: flex; flex-direction: column; align-items: center;
    justify-content: space-around; padding: 60px 0;
  }
  .card {
    position: relative; width: 640px; height: 366px;
    border-radius: 3px; overflow: hidden;
    box-shadow: 0 18px 40px rgba(0,0,0,.45);
  }
  /* Front */
  .card--front {
    background: var(--card-front);
    display: flex; align-items: center; justify-content: center; gap: 22px;
  }
  .front-mark {
    width: 70px; height: 70px;
    border: 6px solid var(--emboss);
  }
  .front-name {
    font-weight: 700; font-size: 40px; letter-spacing: 2px;
    color: var(--emboss-light); text-transform: uppercase;
  }
  /* Back */
  .card--back { background: var(--card-black); color: var(--white); }
  .card-waves { position: absolute; inset: 0; width: 100%; height: 100%; }
  .brand {
    position: absolute; left: 40px; top: 100px;
    display: flex; align-items: center; gap: 14px;
  }
  .brand-square {
    width: 52px; height: 52px; border: 5px solid var(--orange); flex: none;
  }
  .brand-name {
    font-weight: 700; font-size: 30px; line-height: 1.05;
    color: var(--orange); text-transform: uppercase; letter-spacing: 1px;
  }
  .address {
    position: absolute; left: 40px; top: 190px;
    font-size: 17px; line-height: 1.25;
  }
  .person {
    position: absolute; right: 36px; top: 78px; text-align: right;
  }
  .person-name { font-weight: 700; font-size: 28px; line-height: 1.05; }
  .person-title { font-size: 16px; }
  .contacts {
    position: absolute; right: 30px; bottom: 20px;
    list-style: none; text-align: right; font-size: 17px; line-height: 1.3;
  }
  .contacts li { display: flex; align-items: center; justify-content: flex-end; gap: 10px; }
  .contacts svg { width: 15px; height: 15px; fill: var(--orange); flex: none; }
</style>
</head>
<body>
<main class="sheet">

  <section class="card card--front" aria-label="Card front">
    <div class="front-mark"></div>
    <div class="front-name">Lanternfield</div>
  </section>

  <section class="card card--back" aria-label="Card back">
    <svg class="card-waves" viewBox="0 0 640 366" preserveAspectRatio="none" aria-hidden="true">
      <path d="M150 0 H640 V228 C540 220 470 172 410 112 C340 42 260 12 150 0 Z" fill="var(--orange)"/>
      <path d="M0 30 C180 0 330 40 410 110 C470 170 540 215 640 222 L640 234 C536 228 462 184 402 122 C320 52 190 18 0 44 Z" fill="var(--gold)"/>
      <path d="M60 60 C200 30 320 55 395 115 C320 75 220 55 60 60 Z" fill="var(--gold)"/>
    </svg>

    <div class="brand">
      <div class="brand-square"></div>
      <div class="brand-name">Lanternfield<br>Drinks</div>
    </div>

    <p class="address">18 Millbrook Lane,<br>Fairhaven, US 204518</p>

    <div class="person">
      <p class="person-name">Mara Ellison</p>
      <p class="person-title">Managing Director</p>
    </div>

    <ul class="contacts">
      <li>555.218.4470
        <svg viewBox="0 0 16 16"><path d="M3 1h3l1 4-2 1c1 2 3 4 5 5l1-2 4 1v3c0 1-1 2-2 2C7 15 1 9 1 3c0-1 1-2 2-2z"/></svg></li>
      <li>555.930.6612
        <svg viewBox="0 0 16 16"><path d="M4 0h8a1 1 0 0 1 1 1v14a1 1 0 0 1-1 1H4a1 1 0 0 1-1-1V1a1 1 0 0 1 1-1zm1 2v10h6V2zm3 11a1 1 0 1 0 0 2 1 1 0 0 0 0-2z"/></svg></li>
      <li>mara@lanternfield.com
        <svg viewBox="0 0 16 16"><path d="M0 3h16v10H0zm1 1v.5l7 5 7-5V4z"/></svg></li>
      <li>www.lanternfield.com
        <svg viewBox="0 0 16 16"><path d="M8 0a8 8 0 1 0 0 16A8 8 0 0 0 8 0zm-1 1.1V5H4.2C4.8 3 5.8 1.6 7 1.1zm2 0c1.2.5 2.2 1.9 2.8 3.9H9zM3 5H1.7A7 7 0 0 1 5 1.6C4 2.5 3.4 3.7 3 5zm10 0c-.4-1.3-1-2.5-2-3.4A7 7 0 0 1 14.3 5zM1.2 7H3.7v2H1.2a7 7 0 0 1 0-2zm4.5 0H7v2H5.7zm3.3 0h1.3v2H9zm3.3 0h2.5a7 7 0 0 1 0 2h-2.5zM1.7 11H3c.4 1.3 1 2.5 2 3.4A7 7 0 0 1 1.7 11zm2.5 0H7v3.9C5.8 14.4 4.8 13 4.2 11zM9 11h2.8c-.6 2-1.6 3.4-2.8 3.9zm4 0h1.3a7 7 0 0 1-3.3 3.4c1-.9 1.6-2.1 2-3.4z"/></svg></li>
    </ul>
  </section>

</main>
</body>
</html>
```